Business Card Design for company

We want new business cards. We'd like something different-- yet still highly professional. Our tagline is Providing leadership, delivering success. Stock photos are ok, as long as they are relevant and look upscale.

Target Market(s)

Architecture/Business Management Consulting/Engineering Consulting

Contact Information for Business Card

dark gray background with pops of blue might be good, but you tell me. You're the designers. Rounded corners might be nice, but again, you tell me.

Font styles to use
Serif
Sans Serif

Colors
3276b5
5c5c5c
9d9d9d
fbfbfb

Requirements
Nice to have
• Something different, but still very professional.

```html
<!DOCTYPE html>
<html lang="en">
<head>
<meta charset="utf-8">
<title>Halden Group – Business Cards</title>
<link rel="stylesheet" href="https://fonts.googleapis.com/css2?family=Open+Sans:wght@400;600;700&display=swap">
<style>
  :root {
    --brand-blue: #2a6499;
    --brand-blue-bright: #3276b5;
    --slate: #4a4d52;
    --mid-gray: #5c5c5c;
    --light-gray: #9d9d9d;
    --paper: #fbfbfb;
    --backdrop: #1d1d1f;
    --front-top: #858b94;
    --front-bottom: #3f4349;
  }
  * { box-sizing: border-box; margin: 0; padding: 0; }
  html, body {
    width: 1200px;
    height: 885px;
    overflow: hidden;
    background: var(--backdrop);
    font-family: "Open Sans", sans-serif;
  }
  .canvas {
    position: relative;
    width: 1200px;
    height: 885px;
  }
  .card {
    position: absolute;
    width: 560px;
    height: 320px;
    border-radius: 4px;
    overflow: hidden;
    box-shadow: 0 18px 40px rgba(0, 0, 0, 0.55);
  }

  /* Front side */
  .card-front {
    left: 90px;
    top: 80px;
    background: linear-gradient(160deg, var(--front-top) 0%, var(--front-bottom) 70%);
    display: flex;
    flex-direction: column;
    align-items: center;
    justify-content: center;
  }
  .front-wordmark {
    color: var(--paper);
    font-weight: 700;
    font-size: 52px;
    letter-spacing: 4px;
    line-height: 1;
  }
  .front-tagline {
    margin-top: 48px;
    color: var(--paper);
    font-size: 14px;
    letter-spacing: 0.3px;
    display: flex;
    align-items: center;
    gap: 8px;
  }
  .tagline-dot {
    width: 6px;
    height: 6px;
    border-radius: 50%;
    background: var(--paper);
  }

  /* Back side */
  .card-back {
    left: 550px;
    top: 480px;
    background: var(--paper);
  }
  .back-wordmark {
    position: absolute;
    right: 28px;
    top: 38px;
    text-align: right;
    color: var(--mid-gray);
    font-weight: 700;
    font-size: 40px;
    letter-spacing: 3px;
    line-height: 1.1;
  }
  .back-wordmark .wordmark-sub {
    display: block;
    font-size: 40px;
  }
  .name-band {
    position: absolute;
    left: 0;
    top: 168px;
    width: 100%;
    height: 48px;
    background: var(--slate);
    padding: 6px 28px 0 0;
    text-align: right;
    color: var(--paper);
  }
  .person-name {
    font-weight: 700;
    font-size: 17px;
    line-height: 1.1;
  }
  .person-title {
    font-size: 12px;
    letter-spacing: 0.4px;
    line-height: 1.2;
  }
  .contact-band {
    position: absolute;
    left: 0;
    top: 216px;
    width: 100%;
    height: 104px;
    background: var(--brand-blue);
    padding: 14px 28px 0 0;
    text-align: right;
    color: var(--paper);
    font-size: 12.5px;
    line-height: 1.55;
  }
  .contact-label { font-weight: 700; }
</style>
</head>
<body>
<main class="canvas">
  <section class="card card-front" aria-label="Card front">
    <div class="front-wordmark">HALDEN</div>
    <p class="front-tagline">
      <span>Providing leadership</span>
      <span class="tagline-dot"></span>
      <span>delivering success</span>
    </p>
  </section>

  <section class="card card-back" aria-label="Card back">
    <div class="back-wordmark">HALDEN<span class="wordmark-sub">GROUP</span></div>
    <div class="name-band">
      <p class="person-name">MARA LINDQVIST</p>
      <p class="person-title">PRESIDENT</p>
    </div>
    <div class="contact-band">
      <p>2170 Alder Court Ridgeview, NY 10590</p>
      <p><span class="contact-label">P:</span> 555 0142 7781 <span class="contact-label">M:</span> 555 0199 3046 <span class="contact-label">F:</span> 555 0173 5219</p>
      <p><span class="contact-label">E:</span> mara@haldengroup.com <span class="contact-label">W:</span> www.haldengroup.com</p>
    </div>
  </section>
</main>
</body>
</html>
```